Veltrane Group Business Card Design

The CEO is looking for a new trendy look for his business card.
You can stay with current branding or come up with something new/creative. It can be 3D, including Medical Office buildings. You can use our logo in a variety of colors. Please include name, title, company name, company website, email address, cell number

Target Market(s)

Real Estate Development and Construction

Industry/Entity Type

Health care real estate

Contact Information for Business Card

Rohesh Kamdar, CEO M-604.781.2249 E-roheshkamdar@veltrane.com Address:4180 Lindqvist Ave, Corvale, OR 97482 www.veltrane.com

Font styles to use
Other font styles liked:
• Be creative

Requirements
Must have
• Creative, trendy look
Nice to have
• Please go to our website to get a feel- www. veltrane.com
Should not have
• small fonts

```html
<!DOCTYPE html>
<html lang="en">
<head>
<meta charset="utf-8">
<title>Veltrane Group Business Card</title>
<link href="https://fonts.googleapis.com/css2?family=Montserrat:wght@400;500;700;800;900&display=swap" rel="stylesheet">
<style>
  :root {
    --navy: #1b2f52;
    --red: #b31f29;
    --white: #ffffff;
    --ink: #1a1a1a;
    --stage: #e9eaec;
  }
  * { box-sizing: border-box; margin: 0; padding: 0; }
  html, body { width: 1200px; height: 874px; overflow: hidden; }
  body {
    background: var(--stage);
    font-family: "Montserrat", sans-serif;
    display: flex;
    flex-direction: column;
    align-items: center;
    justify-content: center;
    gap: 44px;
  }
  .card {
    width: 660px;
    height: 377px;
    border-radius: 22px;
    position: relative;
    overflow: hidden;
    box-shadow: 0 6px 18px rgba(0,0,0,0.12);
  }
  .card-front {
    background: var(--navy);
    display: flex;
    align-items: center;
    justify-content: center;
  }
  .wordmark {
    font-family: "Montserrat", sans-serif;
    font-weight: 900;
    letter-spacing: -1px;
    line-height: 1;
    white-space: nowrap;
  }
  .card-front .wordmark { color: var(--white); font-size: 64px; }
  .card-back { background: var(--white); }
  .card-back .wordmark {
    position: absolute;
    top: 58px;
    left: 0;
    right: 0;
    text-align: center;
    color: var(--red);
    font-size: 58px;
  }
  .contact-row {
    position: absolute;
    top: 176px;
    left: 0;
    right: 0;
    display: flex;
    justify-content: center;
    gap: 22px;
  }
  .person { text-align: right; padding-top: 4px; }
  .person-name { color: var(--red); font-weight: 700; font-size: 24px; }
  .person-title { color: var(--ink); font-weight: 500; font-size: 16px; margin-top: 2px; }
  .divider { width: 2px; height: 96px; background: var(--red); }
  .details { list-style: none; padding-top: 6px; }
  .details li {
    display: flex;
    align-items: center;
    gap: 10px;
    font-size: 16px;
    font-weight: 500;
    color: var(--ink);
    margin-bottom: 8px;
  }
  .details svg { width: 16px; height: 16px; fill: var(--red); flex: none; }
  .address-band {
    position: absolute;
    left: 0; right: 0; bottom: 0;
    height: 78px;
    background: var(--navy);
    color: var(--white);
    display: flex;
    align-items: center;
    justify-content: center;
    font-size: 17px;
    font-weight: 500;
  }
</style>
</head>
<body>
  <section class="card card-front">
    <div class="wordmark">Veltrane Group</div>
  </section>

  <section class="card card-back">
    <div class="wordmark">Veltrane Group</div>
    <div class="contact-row">
      <div class="person">
        <div class="person-name">Rohesh Kamdar</div>
        <div class="person-title">CEO</div>
      </div>
      <div class="divider"></div>
      <ul class="details">
        <li>
          <svg viewBox="0 0 24 24" aria-hidden="true"><path d="M6.6 10.8a15.2 15.2 0 0 0 6.6 6.6l2.2-2.2a1 1 0 0 1 1-.25 11.4 11.4 0 0 0 3.6.57 1 1 0 0 1 1 1V20a1 1 0 0 1-1 1A17 17 0 0 1 3 4a1 1 0 0 1 1-1h3.5a1 1 0 0 1 1 1c0 1.25.2 2.45.57 3.57a1 1 0 0 1-.25 1z"/></svg>
          604.781.2249
        </li>
        <li>
          <svg viewBox="0 0 24 24" aria-hidden="true"><path d="M2 5h20v14H2z"/><path d="M3 6l9 7 9-7" fill="none" stroke="#fff" stroke-width="1.6"/></svg>
          roheshkamdar@veltrane.com
        </li>
        <li>
          <svg viewBox="0 0 24 24" aria-hidden="true"><circle cx="12" cy="12" r="10"/><path d="M2 12h20M12 2c3 3 3 17 0 20M12 2c-3 3-3 17 0 20" fill="none" stroke="#fff" stroke-width="1.3"/></svg>
          www.veltrane.com
        </li>
      </ul>
    </div>
    <div class="address-band">4180 Lindqvist Ave, Corvale, OR 97482</div>
  </section>
</body>
</html>
```